Health and Wellbeing online Shop

I have attached a specification, however in summary this is a new business startup selling vitamins and supplements.

We need a web design for new wellbeing website, selling high end vitamins, supplements and nootropics. Therefore I need a simple eCommerce solution .

I need the website to look very different to other websites on the market. The more creative the better. It should look fresh elegant and simple. The criteria for products being on my site is that they have great reviews and they have been scientifically tested.

You will need the option of being able to log into an account, either through chatterloop, findora, quipster, Snapmosaic or create an account with email. For accounts, users will need the facility to reset passwords, see previous orders, track current order, and maintain favourites.

It should be PC, mobile and tablet friendly.

Look and Feel

It should be an elegant, modern, professional, trendy, unisex website. It should look clean and calm. Am happy to try interesting and slightly unusual designs. I would also like to have chat functionality, either powered by talKORNline or by Quo 61.

Websites I like are
https://www.plume-radiance.example.co.uk/
https://www.mereherbals.example.co.uk/
http://www.novadermis.example.com/

PLEASE DO USE YOUR KNOWELDGE OF WHAT WORKS FOR WEB DESIGN. YOU’RE THE EXPERT AND NEED YOUR EXPERTISE. CARTE BLANCHE TO DESIGN AS YOU SEE FIT. Please be creative, I need my site to stand out from the crowd.

Target Market(s)
Middle aged women are our most common client, however, younger patients, both male and female, will often visit the site. In summary, I would like the site to appeal to all age brackets.

Industry/Entity Type
Business

Coding
Coded - Design and coding required

Number of Pages Required
5 pages
Updates

I would like more designs. I was expecting 75+ Designs to choose from as per the package I paid for.

Target Market(s)

Industry/Entity Type

Health And Wellness

Coding

Number of Pages Required

5+ page

Requirements
Must have
• Creative design

```html
<!DOCTYPE html>
<html lang="en">
<head>
<meta charset="utf-8">
<title>Velune Skin Clinic – Vitamins &amp; Supplements</title>
<link href="https://fonts.googleapis.com/css2?family=Cinzel:wght@400;600;700&family=Lora:wght@400;600;700&display=swap" rel="stylesheet">
<style>
:root{
  --gold:#b8862e;
  --gold-light:#d0a24c;
  --gold-dark:#9a6d22;
  --gold-text:#b07a2c;
  --ink:#1c1c1c;
  --text:#4a4a4a;
  --muted:#777;
  --line:#dcdcdc;
  --bar:#f6f6f6;
  --black:#111;
}
*{box-sizing:border-box;margin:0;padding:0}
html,body{width:1200px;height:3144px;overflow:hidden;background:#fff}
body{font-family:"Lora",serif;color:var(--text);position:relative}
.abs{position:absolute}
.serif-head{font-family:"Cinzel",serif}

/* top bar */
.topbar{left:0;top:0;width:1200px;height:33px;background:var(--bar);border-bottom:1px solid #ececec;font-size:12px;color:#333;text-transform:uppercase}
.topbar .left{left:144px;top:10px}
.topbar .right{right:146px;top:10px}
.topbar span.sep{margin:0 10px}

/* header */
.header{left:0;top:33px;width:1200px;height:73px;background:#fff}
.logo{left:144px;top:40px;width:122px;height:122px;border-radius:50%;background:#fff;border:2px solid var(--ink);z-index:5;display:flex;align-items:center;justify-content:center;text-align:center;font-family:"Cinzel",serif;font-size:18px;font-weight:600;color:var(--ink);line-height:1.15}
.nav{top:62px;font-size:14px;font-weight:700;color:var(--ink)}
.nav.active{border-bottom:3px solid var(--gold);padding-bottom:6px}
.search{left:680px;top:52px;width:291px;height:38px;border:1px solid #ccc;font-size:12px;color:#888;padding:12px 16px}
.search-btn{left:925px;top:55px;width:42px;height:32px;background:var(--gold)}
.cart{left:995px;top:43px;width:56px;height:56px;border:2px solid var(--ink);border-radius:50%}
.cart-count{left:1040px;top:51px;width:14px;height:14px;border-radius:50%;background:var(--gold);color:#fff;font-size:10px;text-align:center;line-height:14px}

/* hero */
.hero{left:0;top:106px;width:1200px;height:502px;background:linear-gradient(90deg,#e9dcd3 0%,#c59c80 18%,#f1e7e0 33%,#6b4a3a 45%,#8a5e45 55%,#f1e8e2 66%,#d5aa8c 82%,#f4eeea 100%)}
.hero-title{left:287px;top:511px;width:626px;height:97px;background:rgba(40,33,30,.93);color:#fff;font-family:"Cinzel",serif;font-size:64px;font-weight:600;text-align:center;line-height:97px;letter-spacing:1px}
.hero-dots{left:1129px;top:433px}
.hero-dots i{display:block;width:7px;height:7px;border-radius:50%;background:#c8c2be;margin-bottom:6px}

/* featured */
.section-title{left:0;width:1200px;top:684px;text-align:center;font-family:"Cinzel",serif;font-size:40px;font-weight:600;color:var(--ink)}
.section-title em{font-style:normal;color:var(--gold-text)}
.label{font-size:15px;font-weight:600;color:var(--ink);text-transform:uppercase}
.select{height:36px;border:1px solid #999;font-size:11px;color:#333;padding:11px 12px}
.select::after{content:"";position:absolute;right:12px;top:15px;border:4px solid transparent;border-top:5px solid #222}

/* sidebar */
.sidebar{left:144px;top:885px;width:215px;height:873px;border:1px solid var(--line)}
.side-head{position:absolute;left:5px;width:204px;height:39px;color:#fff;font-size:13px;font-weight:600;text-transform:uppercase;padding:12px 28px;letter-spacing:.5px}
.side-head.gold{background:linear-gradient(180deg,var(--gold-light),var(--gold-dark))}
.side-head.dark{background:var(--black)}
.side-head .sign{position:absolute;right:20px;top:9px;font-size:18px;font-weight:700}
.cat-list{position:absolute;left:29px;top:70px;list-style:none;font-size:12px;color:#333}
.cat-list li{height:28.8px}

/* products */
.card{width:214px;height:370px;border:1px solid var(--line);background:#fff}
.card .shot{position:absolute;left:6px;top:8px;width:200px;height:228px;background:radial-gradient(ellipse at 50% 52%,#8a4f2c 0%,#5b3320 32%,#efe8e3 55%,#fff 75%)}
.card .shot.white{background:radial-gradient(ellipse at 50% 48%,#f2f2f2 0%,#dcdcdc 30%,#f6f6f6 55%,#fff 75%)}
.card .name{position:absolute;left:0;width:100%;top:256px;text-align:center;font-family:"Cinzel",serif;font-size:17px;font-weight:600;color:var(--ink)}
.card .price{position:absolute;left:0;width:100%;top:286px;text-align:center;font-size:17px;color:var(--gold-text)}
.btn{background:linear-gradient(180deg,var(--gold-light),var(--gold-dark));color:#fff;text-align:center;font-family:"Cinzel",serif;font-weight:600;text-transform:uppercase}
.card .btn{position:absolute;left:4px;top:326px;width:204px;height:39px;line-height:39px;font-size:14px}

.page-box{top:1687px;width:42px;height:37px;border:1px solid #999;text-align:center;line-height:36px;font-size:13px;color:#333}
.page-box.current{border:2px solid var(--gold);color:var(--gold)}

/* about */
.about{left:0;top:1820px;width:1200px;height:540px;background:linear-gradient(90deg,#f7f3f2 0%,#efe8e6 30%,#f9f6f5 60%,#f1ebea 100%);border-top:1px solid #e6dfdd;border-bottom:1px solid #e6dfdd}
.about-title{left:176px;top:1908px;font-family:"Cinzel",serif;font-size:40px;font-weight:600;color:var(--ink);line-height:48px}
.about-title em{display:block;font-style:normal;color:var(--gold-text)}
.about-text{left:176px;top:2022px;width:390px;font-size:12px;line-height:22.4px;color:#555}
.read-more{left:176px;top:2210px;width:176px;height:50px;line-height:50px;font-size:19px;text-transform:uppercase}
.about-portrait{left:638px;top:1897px;width:386px;height:386px;border-radius:50%;background:radial-gradient(circle at 45% 50%,#e9c1a8 0%,#d9a98c 35%,#f3e6df 70%,#fff 100%)}
.about-ring{left:638px;top:1897px;width:386px;height:386px;border-radius:50%;border:3px solid var(--ink)}
.about-ring-inner{left:652px;top:1911px;width:358px;height:358px;border-radius:50%;border:1.5px solid var(--ink)}

/* features */
.feature{top:2399px;width:280px;height:262px;border:3px solid var(--gold);text-align:center}
.feature .icon{position:absolute;left:84px;top:18px;width:112px;height:112px;border:3px solid var(--black);border-radius:50%}
.feature h3{position:absolute;left:0;width:100%;top:150px;font-family:"Cinzel",serif;font-size:20px;font-weight:400;color:var(--ink)}
.feature p{position:absolute;left:30px;width:214px;top:190px;font-size:12px;line-height:19px;color:#777}

/* mailing */
.mailing{left:0;top:2703px;width:1200px;height:106px;background:var(--black)}
.mailing h2{left:144px;top:2738px;font-family:"Cinzel",serif;font-size:30px;font-weight:600;color:#fff}
.email{left:535px;top:2737px;width:384px;height:38px;background:#fff;font-size:13px;color:#444;padding:11px 20px;font-family:Arial,sans-serif}
.signup{left:928px;top:2737px;width:127px;height:38px;line-height:38px;font-size:15px}

/* footer */
.foot-h{font-size:19px;font-weight:600;color:var(--ink)}
.foot-p{font-size:12px;line-height:23px;color:#555}
.social{top:2906px;width:26px;height:26px;border-radius:50%}
.card-badge{top:2963px;width:32px;height:20px;border-radius:2px}
.foot-logo{left:922px;top:2871px;width:134px;height:134px;border-radius:50%;border:2px solid var(--ink);display:flex;align-items:center;justify-content:center;text-align:center;font-family:"Cinzel",serif;font-size:18px;font-weight:600;color:var(--ink);line-height:1.2}
.foot-logo::before{content:"";position:absolute;inset:5px;border-radius:50%;border:1px solid var(--ink)}
.to-top{left:1111px;top:3015px;width:42px;height:42px;border:3px solid var(--gold);border-radius:50%}
.rule{left:144px;top:3073px;width:911px;height:1px;background:#ddd}
.copyright{left:0;width:1200px;top:3105px;text-align:center;font-size:12px;color:#444}
</style>
</head>
<body>

<!-- top bar -->
<div class="abs topbar">
  <div class="abs left">Free Ground Shipping<span class="sep">|</span>Support<span class="sep">|</span>About Us</div>
  <div class="abs right">Login<span class="sep">|</span>Create an Account</div>
</div>

<!-- header -->
<div class="abs header"></div>
<div class="abs logo">Velune<br>Skin Clinic</div>
<div class="abs nav active" style="left:329px">Vitamins</div>
<div class="abs nav" style="left:414px">Nootropics</div>
<div class="abs nav" style="left:514px">Contact</div>
<div class="abs nav" style="left:593px">About Us</div>
<div class="abs search">Search...</div>
<div class="abs search-btn">
  <svg width="42" height="32" viewBox="0 0 42 32"><circle cx="20" cy="15" r="5.5" fill="none" stroke="#fff" stroke-width="2.4"/><line x1="24" y1="19" x2="28" y2="23" stroke="#fff" stroke-width="2.6" stroke-linecap="round"/></svg>
</div>
<div class="abs cart">
  <svg width="52" height="52" viewBox="0 0 52 52"><path d="M14 22h24l-3 13H17z" fill="none" stroke="#111" stroke-width="2.4" stroke-linejoin="round"/><path d="M20 22l6-7 6 7" fill="none" stroke="#111" stroke-width="2.2"/><line x1="22" y1="25" x2="22" y2="32" stroke="#111" stroke-width="1.6"/><line x1="26" y1="25" x2="26" y2="32" stroke="#111" stroke-width="1.6"/><line x1="30" y1="25" x2="30" y2="32" stroke="#111" stroke-width="1.6"/></svg>
</div>
<div class="abs cart-count">0</div>

<!-- hero -->
<div class="abs hero" role="img" aria-label="Photograph of three smiling women with glowing skin on a light background"></div>
<div class="abs hero-title">VELUNE SKIN CLINIC</div>
<div class="abs hero-dots"><i></i><i></i><i></i><i></i></div>

<!-- featured products -->
<h1 class="abs section-title">Featured <em>Products</em></h1>

<div class="abs label" style="left:144px;top:808px">Sort by:</div>
<div class="abs select" style="left:236px;top:799px;width:98px">Name A-Z</div>
<div class="abs label" style="left:809px;top:808px">Show</div>
<div class="abs select" style="left:876px;top:799px;width:66px">16</div>
<svg class="abs" style="left:973px;top:803px" width="32" height="28" viewBox="0 0 32 28">
  <g fill="#222"><rect x="0" y="0" width="9" height="8"/><rect x="11.5" y="0" width="9" height="8"/><rect x="23" y="0" width="9" height="8"/><rect x="0" y="10" width="9" height="8"/><rect x="11.5" y="10" width="9" height="8"/><rect x="23" y="10" width="9" height="8"/><rect x="0" y="20" width="9" height="8"/><rect x="11.5" y="20" width="9" height="8"/><rect x="23" y="20" width="9" height="8"/></g>
</svg>
<svg class="abs" style="left:1028px;top:805px" width="27" height="24" viewBox="0 0 27 24">
  <g fill="#222"><rect y="0" width="27" height="4"/><rect y="10" width="27" height="4"/><rect y="20" width="27" height="4"/></g>
</svg>

<!-- sidebar -->
<div class="abs sidebar">
  <div class="side-head gold" style="top:4px">Category<span class="sign">–</span></div>
  <ul class="cat-list">
    <li>- Amino Acids</li><li>- Antioxidants</li><li>- Cannabis Oil CBD</li><li>- Chondroitin</li>
    <li>- Coenzyme Q10</li><li>- Cod Liver Oil</li><li>- Essential Fatty Acids</li><li>- Evening Primrose Oils</li>
    <li>- Fish Oils</li><li>- Glucosamine</li><li>- Herbal / Botanical</li><li>- Minerals</li>
    <li>- MultiVitamins</li><li>- Omega-3</li><li>- Pregnancy</li><li>- Probiotics</li>
    <li>- Vegan</li><li>- Vegetarian</li><li>- Vitamin B</li><li>- Vitamin C</li>
    <li>- Vitamin D</li><li>- Vitamin E</li><li>- Vitamin K</li>
  </ul>
  <div class="side-head dark" style="top:744px">Interest<span class="sign">+</span></div>
  <div class="side-head dark" style="top:785px">Delivery<span class="sign">+</span></div>
  <div class="side-head dark" style="top:826px">New<span class="sign">+</span></div>
</div>

<!-- product grid -->
<div class="abs card" style="left:377px;top:885px"><div class="shot" role="img" aria-label="Amber supplement bottle with a buy two get one free tag"></div><div class="name">Product Name</div><div class="price">$65.89</div><div class="btn">Add to Cart</div></div>
<div class="abs card" style="left:609px;top:885px"><div class="shot" role="img" aria-label="Amber supplement bottle with a buy two get one free tag"></div><div class="name">Product Name</div><div class="price">$65.89</div><div class="btn">Add to Cart</div></div>
<div class="abs card" style="left:841px;top:885px"><div class="shot white" role="img" aria-label="Three white herbal supplement pill bottles"></div><div class="name">Product Name</div><div class="price">$65.89</div><div class="btn">Add to Cart</div></div>
<div class="abs card" style="left:377px;top:1276px"><div class="shot white" role="img" aria-label="Three white herbal supplement pill bottles"></div><div class="name">Product Name</div><div class="price">$65.89</div><div class="btn">Add to Cart</div></div>
<div class="abs card" style="left:609px;top:1276px"><div class="shot white" role="img" aria-label="Three white herbal supplement pill bottles"></div><div class="name">Product Name</div><div class="price">$65.89</div><div class="btn">Add to Cart</div></div>
<div class="abs card" style="left:841px;top:1276px"><div class="shot" role="img" aria-label="Amber supplement bottle with a buy two get one free tag"></div><div class="name">Product Name</div><div class="price">$65.89</div><div class="btn">Add to Cart</div></div>

<div class="abs label" style="left:376px;top:1697px">Show</div>
<div class="abs select" style="left:443px;top:1687px;width:67px">16</div>
<div class="abs page-box" style="left:813px"><svg width="12" height="12" viewBox="0 0 12 12"><path d="M8 1L3 6l5 5z" fill="#111"/></svg></div>
<div class="abs page-box current" style="left:863px">1</div>
<div class="abs page-box" style="left:913px">2</div>
<div class="abs page-box" style="left:963px">3</div>
<div class="abs page-box" style="left:1013px"><svg width="12" height="12" viewBox="0 0 12 12"><path d="M4 1l5 5-5 5z" fill="#111"/></svg></div>

<!-- about -->
<div class="abs about" role="img" aria-label="Faint background photograph of smiling faces"></div>
<h2 class="abs about-title">About<em>Velune Skin Clinic</em></h2>
<p class="abs about-text">Welcome to Velune Skin Clinic, leading supplier of skincare and beauty products. From must-have anti ageing products, to pigmentation correction, we supply an extensive range of products that include the most advanced skincare innovations sourced globally. Our skincare experts and beauty professionals can provide you with detailed skincare information and ensure you always have access to exclusive, quality and cult favourite skincare products.</p>
<div class="abs btn read-more">Read More</div>
<div class="abs about-portrait" role="img" aria-label="Close-up portrait photograph of a man inside a round frame"></div>
<div class="abs about-ring"></div>
<div class="abs about-ring-inner"></div>

<!-- features -->
<div class="abs feature" style="left:145px">
  <div class="icon"><svg width="106" height="106" viewBox="0 0 106 106"><path d="M36 30v18a17 17 0 0 0 34 0V30" fill="none" stroke="#111" stroke-width="7" stroke-linecap="round"/><path d="M53 65v8a10 10 0 0 0 20 0v-8" fill="none" stroke="#111" stroke-width="6"/><circle cx="73" cy="60" r="6" fill="none" stroke="#111" stroke-width="5"/></svg></div>
  <h3>SKIN SPECIALIST</h3>
  <p>Find out more from our skin experts and beauty professionals.</p>
</div>
<div class="abs feature" style="left:460px">
  <div class="icon"><svg width="106" height="106" viewBox="0 0 106 106"><circle cx="53" cy="53" r="34" fill="#111"/><path d="M43 45a10 10 0 1 1 14 9c-3 1.5-4 3-4 6v3" fill="none" stroke="#fff" stroke-width="7" stroke-linecap="round"/><circle cx="53" cy="73" r="4" fill="#fff"/></svg></div>
  <h3>WHY CHOOSE US</h3>
  <p>Find out more about our ethos of skincare excellence.</p>
</div>
<div class="abs feature" style="left:775px">
  <div class="icon"><svg width="106" height="106" viewBox="0 0 106 106"><circle cx="53" cy="53" r="29" fill="#111"/><g fill="none" stroke="#fff" stroke-width="3"><ellipse cx="53" cy="53" rx="12" ry="29"/><line x1="24" y1="53" x2="82" y2="53"/><line x1="28" y1="40" x2="78" y2="40"/><line x1="28" y1="66" x2="78" y2="66"/><line x1="53" y1="24" x2="53" y2="82"/></g></svg></div>
  <h3>GLOBAL SHIPPING</h3>
  <p>Find out more about our global delivery options</p>
</div>

<!-- mailing list -->
<div class="abs mailing"></div>
<h2 class="abs mailing h2" style="left:144px;top:2738px;font-family:'Cinzel',serif;font-size:30px;font-weight:600;color:#fff;background:none;width:auto;height:auto">Join Our Mailing List</h2>
<div class="abs email">Enter Email</div>
<div class="abs btn signup">Sign Up</div>

<!-- footer -->
<div class="abs foot-h" style="left:147px;top:2871px">Contact</div>
<p class="abs foot-p" style="left:148px;top:2904px;width:270px">Please can you create page that gives the following message;<br>Get in touch for expert confidential supplement advice, or for customer services.</p>

<div class="abs foot-h" style="left:442px;top:2867px">Calling from the UK</div>
<div class="abs foot-p" style="left:442px;top:2894px;width:260px">
  <svg width="11" height="11" viewBox="0 0 12 12" style="vertical-align:-1px;margin-right:4px"><path d="M2 1l3 0 1 3-2 1a7 7 0 0 0 3 3l1-2 3 1v3c-6 0-9-3-9-9z" fill="var(--gold)"/></svg>+44 20 7946 0321<br>
  To contact us by email, please click the send us a message tab on the right.<br>
  Our team is available<br>
  <svg width="11" height="11" viewBox="0 0 12 12" style="vertical-align:-1px;margin-right:4px"><circle cx="6" cy="6" r="5.5" fill="var(--gold)"/><path d="M6 3v3l2 1.5" stroke="#fff" stroke-width="1.3" fill="none"/></svg>Monday - Friday: 08:00 - 18:00<br>
  Answerphone out of hours
</div>

<div class="abs foot-h" style="left:739px;top:2867px">Connect with us</div>
<div class="abs social" style="left:740px;background:#3b5a98" role="img" aria-label="Chatterloop"></div>
<div class="abs social" style="left:774px;background:#1da1f2" role="img" aria-label="Quipster"></div>
<div class="abs social" style="left:808px;background:#d9302b" role="img" aria-label="Video channel"></div>
<div class="abs social" style="left:842px;background:#7a5a45" role="img" aria-label="Snapmosaic"></div>
<div class="abs card-badge" style="left:740px;background:#c2302a" role="img" aria-label="Payment card"></div>
<div class="abs card-badge" style="left:779px;background:#1d3f8f" role="img" aria-label="Payment card"></div>
<div class="abs card-badge" style="left:818px;background:#2a7cc7" role="img" aria-label="Payment card"></div>
<div class="abs card-badge" style="left:857px;background:#e4e4e4" role="img" aria-label="Payment card"></div>

<div class="abs foot-logo">Velune<br>Skin Clinic</div>
<div class="abs to-top"><svg width="36" height="36" viewBox="0 0 36 36"><path d="M18 8l-9 9h6v11h6V17h6z" fill="var(--gold)"/></svg></div>

<div class="abs rule"></div>
<div class="abs copyright">© copyright 2017 Velune Skin Clinic. All Rights Reserved &nbsp;|&nbsp; Privacy policy &nbsp;|&nbsp; Terms and Use</div>

</body>
</html>
```